Business card for law firm

Need business card for new law firm. Think confident, authoritative, conservative, but not stuffy or old-fashioned.

Contact Information for Business Card

Content for card - logo (uploaded), plus the following:

Paul Whitcombe (larger font)
Managing Partner (larger font, but not as large as name)
Level 9, 7 Ferris Lane
Sydney NSW 2000
Main Tel 02 9364 2710
Direct Tel 02 8472 3159
Email paul@qvlegal.com.au
www.qvlegal.com.au

Letterhead design should include logo plus:
Level 9, 7 Ferris Lane
Sydney NSW 2000
Tel 02 8472 3159
www.qvlegal.com.au

```html
<!DOCTYPE html>
<html lang="en">
<head>
<meta charset="utf-8">
<title>Quayvale Lawyers – Letterhead</title>
<link rel="stylesheet" href="https://fonts.googleapis.com/css2?family=Didact+Gothic&family=Old+Standard+TT&display=swap">
<style>
  :root {
    --backdrop: #e6e6e6;
    --sheet-top: #f7f7f7;
    --sheet-bottom: #e2e2e2;
    --navy: #2b3a78;
    --mark-navy: #25326e;
    --brand-grey: #5f5f5f;
    --body-grey: #7a7a7a;
    --band: #0b0b0b;
    --band-text: #ffffff;
    --signature-ink: #c9d3e8;
  }
  * { box-sizing: border-box; margin: 0; padding: 0; }
  html, body {
    width: 1024px;
    height: 1200px;
    overflow: hidden;
    background: var(--backdrop);
  }
  .letterhead {
    position: absolute;
    left: 102px;
    top: 26px;
    width: 820px;
    height: 1148px;
    background: linear-gradient(160deg, var(--sheet-top) 0%, var(--sheet-bottom) 100%);
    box-shadow: 0 2px 14px rgba(0,0,0,0.12);
    font-family: "Didact Gothic", "Century Gothic", sans-serif;
    color: var(--body-grey);
  }
  .brand {
    position: absolute;
    left: 74px;
    top: 118px;
    display: flex;
    align-items: center;
    gap: 12px;
  }
  .brand-square {
    display: block;
    width: 30px;
    height: 30px;
    background: var(--mark-navy);
  }
  .brand-name {
    font-family: "Didact Gothic", "Century Gothic", sans-serif;
    font-size: 22px;
    font-weight: 400;
    color: var(--brand-grey);
    white-space: nowrap;
  }
  .sender-address {
    position: absolute;
    left: 597px;
    top: 108px;
    font-family: "Old Standard TT", Georgia, serif;
    font-style: normal;
    font-size: 15px;
    line-height: 18.5px;
    color: var(--navy);
  }
  .letter-body {
    position: absolute;
    left: 78px;
    top: 324px;
    width: 677px;
  }
  .letter-body .salutation {
    font-size: 19px;
    line-height: 23px;
    color: #7d7d7d;
    margin-bottom: 34px;
  }
  .letter-body p {
    font-size: 12px;
    line-height: 14.8px;
    margin-bottom: 29px;
  }
  .letter-body .closing {
    margin-top: 16px;
    margin-bottom: 0;
  }
  .signature {
    display: block;
    width: 142px;
    height: 66px;
    margin-top: 46px;
    border-radius: 30px;
    background: radial-gradient(ellipse at center, var(--signature-ink) 0%, rgba(201,211,232,0) 72%);
  }
  .footer-band {
    position: absolute;
    left: 0;
    right: 0;
    top: 1082px;
    height: 30px;
    background: var(--band);
  }
  .footer-web {
    position: absolute;
    left: 0;
    width: 782px;
    top: 0;
    line-height: 30px;
    text-align: center;
    font-family: "Old Standard TT", Georgia, serif;
    font-size: 13px;
    letter-spacing: 2.5px;
    color: var(--band-text);
  }
  .footer-square {
    position: absolute;
    left: 660px;
    top: -3px;
    width: 36px;
    height: 36px;
    border: 5px solid var(--sheet-bottom);
    border-top-width: 3px;
    border-bottom-width: 3px;
    background: var(--mark-navy);
  }
</style>
</head>
<body>
  <main class="letterhead">
    <header>
      <div class="brand">
        <span class="brand-square"></span>
        <span class="brand-name">Quayvale Lawyers</span>
      </div>
      <address class="sender-address">
        Level 9, 7 Ferris Lane<br>
        Sydney NSW 2000<br>
        02 8472 3159
      </address>
    </header>

    <section class="letter-body">
      <p class="salutation">Dear Mr. Harlow,</p>
      <p>Lorem ipsum dolor sit amet, consectetur adipiscing elit. Donec orci purus, luctus vitae dignissim eu, iaculis sed purus. Vivamus faucibus, ipsum nec aliquet viverra, leo mauris condimentum ligula, sit amet sagittis enim ligula quis arcu. Nam egestas tortor id nisi porttitor mattis. In tortor ante, ultricies in suscipit a, tempus non massa. Vivamus et auctor mi. Fusce vel massa nulla. Phasellus nec eros mauris, et scelerisque orci.</p>
      <p>Donec malesuada orci vitae nulla accumsan porta a id massa. Quisque accumsan iaculis magna sit amet fringilla. Maecenas consequat, magna eget tincidunt semper, odio nibh rutrum mi, id feugiat ante nisi eu risus. Vestibulum nunc orci, rhoncus a placerat in, ultricies in mi. Cras mattis varius eros, vel fringilla nisi suscipit eget. Quisque scelerisque sagittis nulla at porttitor.</p>
      <p>Sed id augue vitae urna euismod commodo aliquet a quam. Pellentesque arcu velit, cursus et malesuada ut, consequat et diam. Nullam erat sem, rhoncus id ullamcorper vitae, rhoncus et arcu. In ultricies ultricies nulla, ut rutrum nisi iaculis at. Donec eu magna a metus ornare faucibus. Fusce aliquet faucibus ultricies. Morbi semper, est id tincidunt gravida, sem arcu adipiscing lacus, ac bibendum nulla leo eu purus. Quisque nec diam sed risus consectetur a ccumsan quis quis nibh. Vestibulum id purus lorem.</p>
      <p>It is a long established fact that a reader will be distracted by the readable content of a page when looking at its layout. The point of using Lorem Ipsum is that it has a more-or-less normal distribution of letters, as opposed to using 'Content here, content here', making it look like readable English. Many desktop publishing packages</p>
      <p class="closing">Sincerely,</p>
      <span class="signature" role="img" aria-label="Handwritten signature of James Harlow in blue ink"></span>
    </section>

    <footer class="footer-band">
      <span class="footer-web">www.qvlegal.com.au</span>
      <span class="footer-square"></span>
    </footer>
  </main>
</body>
</html>
```